First Annual Whitaker Family Reunion

Family reunion invitation, please see the attached letter for the language. Also provided a picture of my grandparents, if you could include it on a letter or brochure. I'm flexible.
Updates

I just uploaded a Word document with the time, address, and list of activities. Please click on the hyperlink, it takes you directly to our Family Reunion webpage and click on Agenda for all details.

Target Market(s)

Family and Friends invitation

Requirements
Must have
• Date, time, picture, family logo, and website for payment

```html
<!DOCTYPE html>
<html lang="en">
<head>
<meta charset="utf-8">
<title>First Annual Whitaker Family Reunion</title>
<link rel="stylesheet" href="https://fonts.googleapis.com/css2?family=Jost:wght@400;500&display=swap">
<style>
  :root {
    --purple: #5a0fa6;
    --white: #ffffff;
    --ink: #1c1c1c;
    --page: #ffffff;
  }
  * { box-sizing: border-box; margin: 0; padding: 0; }
  html, body { width: 986px; height: 1200px; overflow: hidden; background: var(--page); }
  body { font-family: "Jost", sans-serif; color: var(--ink); }

  .invitation { position: relative; width: 986px; height: 1200px; background: var(--page); }

  .masthead {
    position: absolute; left: 0; top: 0; width: 986px; height: 228px;
    background: var(--purple); color: var(--white);
  }
  .family-mark {
    position: absolute; left: 44px; top: 52px; width: 190px;
    font-weight: 400; font-size: 27px; line-height: 1.12; letter-spacing: 1px;
    color: var(--white);
  }
  .family-mark .mark-square {
    display: block; width: 26px; height: 26px; background: var(--white); margin-bottom: 12px;
  }
  .headline {
    position: absolute; left: 250px; right: 0; top: 38px; text-align: center;
    font-weight: 400; color: var(--white);
  }
  .headline .series { font-size: 60px; line-height: 64px; letter-spacing: 2px; }
  .headline .event { font-size: 52px; line-height: 58px; }
  .headline .date { font-size: 38px; line-height: 50px; }

  .letter {
    position: absolute; left: 45px; top: 250px; width: 432px;
    font-size: 16px; line-height: 23px; text-align: justify;
  }
  .letter p { margin-bottom: 23px; }
  .letter p.sign-off { margin-bottom: 0; text-align: left; }
  .letter a { color: var(--ink); }

  .gallery {
    position: absolute; left: 518px; top: 253px; width: 426px;
    display: grid; grid-template-columns: 194px 194px; column-gap: 38px; row-gap: 15px;
  }
  .photo-frame {
    width: 194px; height: 204px; border: 3px solid var(--purple); padding: 4px; background: var(--white);
  }
  .photo-fill { width: 100%; height: 100%; }
  .fill-grandparents { background: linear-gradient(160deg, #f4f1ec, #d9d2c4); }
  .fill-group-tv { background: linear-gradient(160deg, #3d4f7a, #6a3a3a); }
  .fill-selfie { background: linear-gradient(160deg, #c9b38a, #3a2a25); }
  .fill-park { background: linear-gradient(160deg, #4f6b3a, #8a3b48); }
  .fill-couple { background: linear-gradient(160deg, #c59a6a, #2f2a2e); }
  .fill-party { background: linear-gradient(160deg, #b9a88f, #7a1f2a); }
  .fill-gown { background: linear-gradient(160deg, #c8c2b8, #1e1c1e); }
  .fill-graduate { background: linear-gradient(160deg, #e0a83a, #1f5aa8); }

  .footer-band {
    position: absolute; left: 0; bottom: 0; width: 986px; height: 62px;
    background: var(--purple); display: flex; align-items: center; justify-content: center;
  }
  .footer-band a {
    color: var(--white); font-size: 29px; letter-spacing: 3px; text-decoration: underline;
    text-underline-offset: 4px; text-decoration-thickness: 2px;
  }
</style>
</head>
<body>
<main class="invitation">
  <header class="masthead">
    <div class="family-mark">
      <span class="mark-square"></span>
      Whitaker<br>Family<br>Reunion
    </div>
    <div class="headline">
      <div class="series">First Annual</div>
      <div class="event">Whitaker Family Reunion</div>
      <div class="date">April 7, 2023</div>
    </div>
  </header>

  <section class="letter">
    <p>Dear Family,</p>
    <p>I hope this letter finds all of you in good health and high spirits. Our family, which is spread across different parts of the country, rarely gets an opportunity to gather together under one roof, but I am excited to inform you that we have finally planned a family reunion.</p>
    <p>It has been long overdue, and we are looking forward to catching up with everyone, reminiscing old memories, and creating some new ones over the course of this event. I cannot emphasize enough on how important this reunion will be for our family. We have come to learn over the years that nothing can ever replace the love and connections that we share between us.</p>
    <p>Our family reunion will be from September 1, 2023, through September 3, 2023. We will have a fun-filled weekend filled with activities for all ages, which will include games, music, storytelling, and much more. It is a chance for our family to get to know new members, spend time with those we know and love, and to make it a memorable experience.</p>
    <p>Please RSVP and pay your deposit as soon as possible at <a href="#">www.whitakerreunion.net</a> so that we can make arrangements accordingly. Also, please notify any family members who may have been left out or forgotten.</p>
    <p class="sign-off">I cannot wait to see all of you soon and spend quality time together as a family.<br>As ever,<br>The Whitaker Family Committee</p>
  </section>

  <section class="gallery">
    <div class="photo-frame"><div class="photo-fill fill-grandparents" role="img" aria-label="Photo of the grandparents holding a small grandchild"></div></div>
    <div class="photo-frame"><div class="photo-fill fill-group-tv" role="img" aria-label="Photo of four family members standing in front of a television"></div></div>
    <div class="photo-frame"><div class="photo-fill fill-selfie" role="img" aria-label="Selfie photo of two smiling family members"></div></div>
    <div class="photo-frame"><div class="photo-fill fill-park" role="img" aria-label="Photo of two family members walking in a park"></div></div>
    <div class="photo-frame"><div class="photo-fill fill-couple" role="img" aria-label="Photo of a couple posing together indoors"></div></div>
    <div class="photo-frame"><div class="photo-fill fill-party" role="img" aria-label="Photo of a group of relatives gathered at a table"></div></div>
    <div class="photo-frame"><div class="photo-fill fill-gown" role="img" aria-label="Photo of a relative wearing a black gown"></div></div>
    <div class="photo-frame"><div class="photo-fill fill-graduate" role="img" aria-label="Photo of a young graduate in cap and gown"></div></div>
  </section>

  <footer class="footer-band">
    <a href="#">www.whitakerreunion.net</a>
  </footer>
</main>
</body>
</html>
```